Business Card Design

We need a business card designed for our new company. Prefer a black card with white logo & writing.

Contact Information for Business Card

Ted Galloway, address: 7-4812 Fernhollow Road, Abbotsford, BC, V3K 8R2, Office Phone: 604-712-3390, Cell: 604-947-2164, Email: ted@resinworkshub.ca

Colors

Designer to choose only greyscale colors for use in the design.

```html
<!DOCTYPE html>
<html lang="en">
<head>
<meta charset="utf-8">
<title>Resinworks Hub – Business Card</title>
<link href="https://fonts.googleapis.com/css2?family=Poppins:wght@300;400;700&display=swap" rel="stylesheet">
<style>
  :root {
    --backdrop: #222223;
    --card: #2a2a2c;
    --card-edge: #3a3a3d;
    --deboss: #151516;
    --ink: #ffffff;
    --ink-soft: #e6e6e6;
  }
  * { box-sizing: border-box; margin: 0; padding: 0; }
  html, body {
    width: 1200px; height: 711px; overflow: hidden;
    background: var(--backdrop);
    font-family: "Poppins", sans-serif;
    color: var(--ink);
  }
  .stage {
    position: relative; width: 1200px; height: 711px;
    display: flex; align-items: center; justify-content: center; gap: 40px;
  }
  .card {
    position: relative; width: 540px; height: 309px;
    background: var(--card);
    border: 1px solid var(--card-edge);
    border-radius: 18px;
    overflow: hidden;
  }
  /* Front */
  .card-front { display: flex; align-items: center; justify-content: center; }
  .brand-deboss {
    font-weight: 700; font-size: 44px; letter-spacing: 1px;
    text-transform: uppercase; color: var(--deboss);
  }
  /* Back */
  .brand-mark {
    position: absolute; top: 38px; right: 40px;
    font-weight: 700; font-size: 26px; text-transform: uppercase;
    letter-spacing: 0.5px; color: var(--ink); line-height: 1;
  }
  .identity { position: absolute; left: 0; top: 104px; display: flex; align-items: stretch; }
  .identity-bar { width: 16px; background: var(--ink); margin-right: 12px; }
  .identity-name { font-size: 30px; line-height: 1.05; font-weight: 300; }
  .identity-name strong { font-weight: 700; }
  .identity-title { font-size: 14px; font-weight: 400; color: var(--ink-soft); margin-top: 2px; }
  .contacts {
    position: absolute; right: 26px; top: 150px;
    list-style: none; display: flex; flex-direction: column; gap: 5px;
  }
  .contacts li {
    display: flex; align-items: center; justify-content: flex-end; gap: 10px;
    font-size: 13px; font-weight: 300;
  }
  .contacts svg { width: 14px; height: 14px; fill: none; stroke: var(--ink); stroke-width: 1.6; }
  .address {
    position: absolute; left: 30px; bottom: 26px;
    font-size: 13px; font-weight: 300; line-height: 1.45; font-style: normal;
  }
</style>
</head>
<body>
<main class="stage">
  <section class="card card-front" aria-label="Card front">
    <span class="brand-deboss">Resinworks Hub</span>
  </section>

  <section class="card card-back" aria-label="Card back">
    <div class="brand-mark">Resinworks Hub</div>

    <div class="identity">
      <span class="identity-bar"></span>
      <div>
        <h1 class="identity-name"><strong>Ted</strong> Galloway</h1>
        <p class="identity-title">Founder &amp; CEO</p>
      </div>
    </div>

    <ul class="contacts">
      <li>604-712-3390
        <svg viewBox="0 0 16 16"><path d="M4 2l2.5 3-1.5 1.5c1 2 2.5 3.5 4.5 4.5L11 9.5l3 2.5-1.5 2C7 14 2 9 2 3.5z"/></svg>
      </li>
      <li>604-947-2164
        <svg viewBox="0 0 16 16"><rect x="4" y="1.5" width="8" height="13" rx="1.5"/><line x1="7" y1="12" x2="9" y2="12"/></svg>
      </li>
      <li>www.resinworkshub.ca
        <svg viewBox="0 0 16 16"><circle cx="8" cy="8" r="6"/><ellipse cx="8" cy="8" rx="2.5" ry="6"/><line x1="2" y1="8" x2="14" y2="8"/></svg>
      </li>
      <li>ted@resinworkshub.ca
        <svg viewBox="0 0 16 16"><rect x="1.5" y="3.5" width="13" height="9" rx="1"/><path d="M1.5 4l6.5 5 6.5-5"/></svg>
      </li>
    </ul>

    <address class="address">
      7-4812 Fernhollow Road,<br>
      Abbotsford, BC, V3K 8R2.
    </address>
  </section>
</main>
</body>
</html>
```